Business Card For Halvenmoor Financial Consulting

Hi, I would like a business card designed. Bold, modern.
Please use the same design as the logo. I have also attached the website design to see the overall theme.
Wordmark Font
Color: Hex: #01AEF7

```html
<!DOCTYPE html>
<html lang="en">
<head>
<meta charset="utf-8">
<title>Halvenmoor Financial Consulting – Business Card</title>
<link rel="stylesheet" href="https://fonts.googleapis.com/css2?family=Montserrat:wght@400;500;700&display=swap">
<style>
  :root {
    --bg: #2a2b2d;
    --brand-blue: #01aef7;
    --front-dark: #15222c;
    --front-light: #2f424f;
    --back-dark: #08090b;
    --back-mid: #15191e;
    --glow: #0a7fd8;
    --text: #f2f5f7;
  }
  * { box-sizing: border-box; margin: 0; padding: 0; }
  html, body { width: 1200px; height: 960px; overflow: hidden; }
  body {
    background: var(--bg);
    font-family: "Montserrat", sans-serif;
    color: var(--text);
    position: relative;
  }
  .card {
    position: absolute;
    left: 240px;
    width: 720px;
    height: 411px;
    border-radius: 4px;
    overflow: hidden;
    box-shadow: 0 18px 40px rgba(0,0,0,.45);
  }
  /* Front: contact side */
  .card--front {
    top: 36px;
    background: radial-gradient(ellipse at 55% 55%, var(--front-light) 0%, var(--front-dark) 70%);
  }
  .wordmark {
    position: absolute;
    left: 300px;
    top: 48px;
    font-weight: 700;
    color: var(--text);
    line-height: 1;
  }
  .wordmark__name { display: block; font-size: 46px; letter-spacing: 3px; }
  .wordmark__sub { display: block; font-size: 14px; letter-spacing: 19px; margin-top: 10px; }
  .holder {
    position: absolute;
    left: 40px;
    top: 150px;
  }
  .holder__name {
    position: relative;
    padding-left: 54px;
    font-size: 26px;
    font-weight: 500;
    color: var(--brand-blue);
    letter-spacing: .5px;
  }
  .holder__name::before {
    content: "";
    position: absolute;
    left: 0; top: 50%;
    width: 40px; height: 1.5px;
    background: var(--brand-blue);
  }
  .holder__title { padding-left: 54px; font-size: 15px; margin-top: 2px; }
  .contact-list {
    list-style: none;
    position: absolute;
    left: 40px;
    top: 240px;
    font-size: 16px;
    line-height: 1.6;
  }
  .contact-list li { display: flex; align-items: center; gap: 12px; }
  .contact-list svg { width: 16px; height: 16px; fill: var(--brand-blue); flex: none; }
  .contact-list .address { padding-left: 28px; }

  /* Back: brand side */
  .card--back {
    top: 513px;
    background: linear-gradient(160deg, var(--back-mid) 0%, var(--back-dark) 60%);
  }
  .card--back .wordmark { left: 200px; top: 50px; }
  .chart-art {
    position: absolute;
    left: 60px;
    right: 40px;
    bottom: 30px;
    height: 210px;
    background:
      radial-gradient(ellipse at 50% 85%, rgba(1,174,247,.55) 0%, rgba(10,127,216,.25) 35%, transparent 70%),
      linear-gradient(180deg, transparent 0%, rgba(10,127,216,.15) 100%);
  }
</style>
</head>
<body>

<section class="card card--front" aria-label="Business card front">
  <div class="wordmark">
    <span class="wordmark__name">HALVENMOOR</span>
    <span class="wordmark__sub">CONSULTING</span>
  </div>

  <div class="holder">
    <p class="holder__name">MARCUS DELANE</p>
    <p class="holder__title">Chairman</p>
  </div>

  <ul class="contact-list">
    <li>
      <svg viewBox="0 0 24 24" aria-hidden="true"><path d="M6.6 10.8a15.1 15.1 0 0 0 6.6 6.6l2.2-2.2c.3-.3.7-.4 1-.2 1.1.4 2.3.6 3.6.6.6 0 1 .4 1 1V20c0 .6-.4 1-1 1C10.6 21 3 13.4 3 4c0-.6.4-1 1-1h3.5c.6 0 1 .4 1 1 0 1.3.2 2.5.6 3.6.1.3 0 .7-.2 1z"/></svg>
      +1 555 204 7316
    </li>
    <li>
      <svg viewBox="0 0 24 24" aria-hidden="true"><path d="M2 5h20v14H2zm2 2v.5l8 5 8-5V7zm0 2.8V17h16V9.8l-8 5z"/></svg>
      halvenmoorfinancial@mailbox.com
    </li>
    <li>
      <svg viewBox="0 0 24 24" aria-hidden="true"><path d="M12 2a10 10 0 1 0 0 20 10 10 0 0 0 0-20zm6.9 6h-3a15 15 0 0 0-1.3-3.9A8 8 0 0 1 18.9 8zM12 4c.8 1.2 1.5 2.5 1.9 4h-3.8c.4-1.5 1.1-2.8 1.9-4zM4.3 14a8 8 0 0 1 0-4h3.4a16 16 0 0 0 0 4zm.8 2h3a15 15 0 0 0 1.3 3.9A8 8 0 0 1 5.1 16zm3-8h-3a8 8 0 0 1 4.3-3.9A15 15 0 0 0 8.1 8zM12 20c-.8-1.2-1.5-2.5-1.9-4h3.8c-.4 1.5-1.1 2.8-1.9 4zm2.3-6H9.7a14 14 0 0 1 0-4h4.6a14 14 0 0 1 0 4zm.3 5.9a15 15 0 0 0 1.3-3.9h3a8 8 0 0 1-4.3 3.9zm1.7-5.9a16 16 0 0 0 0-4h3.4a8 8 0 0 1 0 4z"/></svg>
      www.halvenmoorfinancial.com
    </li>
    <li class="address">1820 Larkfield Row Suite 14,<br>East Corrinvale</li>
  </ul>
</section>

<section class="card card--back" aria-label="Business card back">
  <div class="wordmark">
    <span class="wordmark__name">HALVENMOOR</span>
    <span class="wordmark__sub">CONSULTING</span>
  </div>
  <div class="chart-art" role="img" aria-label="Glowing blue 3D bar chart rising along a neon light line"></div>
</section>

</body>
</html>
```